Agriculture Business Card

I want to use my existing logo and use my tagline of "Don't Guess...Soil Test" on the card. Looking for a double sided card that will really get peoples attention.
Contact Info:
Marlow Field Crop Edge
Calvin Brusk
2917 K Lane
Larkin, NE 68593
402-555-0193
calvin.r.brusk@fieldmailbox.net

```html
<!DOCTYPE html>
<html lang="en">
<head>
<meta charset="utf-8">
<title>Marlow Field Crop Edge – Business Card</title>
<link rel="stylesheet" href="https://fonts.googleapis.com/css2?family=Oswald:wght@500;600&family=Open+Sans:wght@400;600&display=swap">
<style>
  :root {
    --page: #3a3d42;
    --card: #1d1d1f;
    --brown: #9a5f44;
    --gold: #f4b91c;
    --green: #2f8f2a;
    --ink: #e8e8e8;
    --muted: #a9a9a9;
    --ghost: #2c2c2f;
  }
  * { margin: 0; padding: 0; box-sizing: border-box; }
  html, body { width: 1200px; height: 900px; overflow: hidden; }
  body {
    background: var(--page);
    display: flex;
    flex-direction: column;
    align-items: center;
    justify-content: center;
    gap: 40px;
    font-family: "Open Sans", sans-serif;
  }
  .card {
    position: relative;
    width: 700px;
    height: 400px;
    background: var(--card);
    border-radius: 28px;
    overflow: hidden;
  }

  /* Front side */
  .card-front .edge-band {
    position: absolute;
    left: 0; bottom: 0;
    width: 100%; height: 16px;
  }
  .card-front .holder {
    position: absolute;
    left: 44px; top: 48px;
  }
  .holder-name {
    font-family: "Oswald", sans-serif;
    font-weight: 600;
    font-size: 34px;
    letter-spacing: 1px;
    color: var(--brown);
    text-transform: uppercase;
    line-height: 1.1;
  }
  .holder-title {
    font-size: 15px;
    color: var(--muted);
    margin-top: 4px;
  }
  .divider {
    position: absolute;
    left: 44px; right: 44px; top: 200px;
    height: 1px;
    background: var(--green);
  }
  .contact-list {
    position: absolute;
    left: 44px; top: 222px;
    list-style: none;
  }
  .contact-list li, .address {
    display: flex;
    align-items: center;
    gap: 10px;
    font-size: 16px;
    color: var(--ink);
    margin-bottom: 12px;
  }
  .contact-list svg, .address svg { width: 16px; height: 16px; fill: var(--gold); flex: none; }
  .address {
    position: absolute;
    right: 44px; top: 300px;
    font-size: 18px;
  }
  .brand {
    position: absolute;
    right: 44px; top: 56px;
    display: flex;
    align-items: center;
    gap: 12px;
  }
  .brand-dot {
    width: 26px; height: 26px;
    background: var(--gold);
    border-radius: 50%;
  }
  .brand-name {
    font-family: "Oswald", sans-serif;
    font-weight: 500;
    font-size: 24px;
    color: var(--brown);
    line-height: 1.15;
    text-align: left;
  }

  /* Back side */
  .card-back {
    display: flex;
    flex-direction: column;
    align-items: center;
    justify-content: center;
  }
  .back-mark {
    font-family: "Oswald", sans-serif;
    font-weight: 600;
    font-size: 52px;
    color: var(--ghost);
    text-align: center;
    line-height: 1.1;
  }
  .tagline {
    position: absolute;
    left: 140px; bottom: 78px;
    font-size: 22px;
    color: var(--gold);
  }
</style>
</head>
<body>

  <section class="card card-front" aria-label="Business card front">
    <svg class="edge-band" viewBox="0 0 700 16" preserveAspectRatio="none" aria-hidden="true">
      <polygon points="0,0 390,0 380,16 0,16" fill="var(--gold)"/>
      <polygon points="390,0 700,0 700,16 380,16" fill="var(--brown)"/>
    </svg>

    <div class="holder">
      <h1 class="holder-name">Calvin Brusk</h1>
      <p class="holder-title">CEO/Founder</p>
    </div>

    <div class="brand">
      <span class="brand-dot"></span>
      <span class="brand-name">Marlow Field<br>Crop Edge</span>
    </div>

    <div class="divider"></div>

    <ul class="contact-list">
      <li>
        <svg viewBox="0 0 24 24" aria-hidden="true"><path d="M6.6 10.8a15.1 15.1 0 0 0 6.6 6.6l2.2-2.2a1 1 0 0 1 1-.25 11.4 11.4 0 0 0 3.6.57 1 1 0 0 1 1 1V20a1 1 0 0 1-1 1A17 17 0 0 1 3 4a1 1 0 0 1 1-1h3.5a1 1 0 0 1 1 1c0 1.25.2 2.45.57 3.6a1 1 0 0 1-.25 1z"/></svg>
        402-555-0193
      </li>
      <li>
        <svg viewBox="0 0 24 24" aria-hidden="true"><path d="M2 5h20v14H2z M3.5 6.5 12 13l8.5-6.5" fill="var(--gold)" stroke="var(--card)" stroke-width="1.5"/></svg>
        calvin.r.brusk@fieldmailbox.net
      </li>
    </ul>

    <p class="address">
      <svg viewBox="0 0 24 24" aria-hidden="true"><path d="M12 2a7 7 0 0 0-7 7c0 5.2 7 13 7 13s7-7.8 7-13a7 7 0 0 0-7-7zm0 9.5A2.5 2.5 0 1 1 12 6.5a2.5 2.5 0 0 1 0 5z"/></svg>
      2917 K Lane Larkin, NE 68593
    </p>
  </section>

  <section class="card card-back" aria-label="Business card back">
    <p class="back-mark">Marlow Field<br>Crop Edge</p>
    <p class="tagline">Don't Guess...Soil Test</p>
  </section>

</body>
</html>
```